Coastline Premier Retreats Business Card Design

Design a business card for Coastline Premier Retreats. Look at the website for colors and reference. Card should have logo, name, title, office number, mobile number, email, URL and a tagline like, "Luxury Hotel & Resort Email Marketing" (This might change).

https://www.coastlinepremierretreats.example

The rest I will leave up to your imagination.

Contact Information for Business Card

Logo, name, title, office number, mobile number, email, URL and a tagline like, "Luxury Hotel & Resort Email Marketing" (This might change).

```html
<!DOCTYPE html>
<html lang="en">
<head>
<meta charset="utf-8">
<title>Coastline Premier Retreats – Business Card</title>
<link rel="stylesheet" href="https://fonts.googleapis.com/css2?family=Arimo:wght@400;700&display=swap">
<style>
  :root {
    --page: #2b2b2b;
    --card: #1b1b1b;
    --orange: #e87118;
    --white: #f2f2f2;
    --emboss: #3a3a3a;
  }
  * { margin: 0; padding: 0; box-sizing: border-box; }
  html, body { width: 1200px; height: 1059px; overflow: hidden; }
  body {
    background: var(--page);
    font-family: "Arimo", Arial, sans-serif;
    position: relative;
  }
  .card {
    position: absolute;
    background: var(--card);
    box-shadow: 0 10px 24px rgba(0,0,0,0.45);
  }
  .card-front { left: 256px; top: 89px; width: 688px; height: 390px; }
  .card-back  { left: 254px; top: 547px; width: 693px; height: 394px; }

  .brand-name {
    position: absolute;
    left: 56px; top: 158px; width: 258px;
    color: var(--white);
    font-weight: 700;
    font-size: 22px;
    line-height: 26px;
    letter-spacing: 1px;
    text-transform: uppercase;
    text-align: center;
  }
  .divider {
    position: absolute;
    left: 347px; top: 90px;
    width: 1px; height: 189px;
    background: var(--orange);
  }
  .contact-block {
    position: absolute;
    left: 376px; top: 84px;
    color: var(--white);
  }
  .person-name {
    color: var(--orange);
    font-weight: 700;
    font-size: 29px;
    line-height: 34px;
    letter-spacing: 0.3px;
  }
  .person-title { font-size: 16px; line-height: 20px; margin-top: 1px; }
  .address { font-size: 16px; line-height: 20px; margin-top: 13px; }
  .contact-list { list-style: none; margin-top: 10px; }
  .contact-list li {
    display: flex; align-items: center;
    font-size: 16px; line-height: 21.5px;
    white-space: nowrap;
  }
  .contact-list svg { width: 12px; height: 12px; margin-right: 7px; flex: none; fill: var(--orange); }
  .tagline-band {
    position: absolute;
    left: 0; top: 327px; width: 100%; height: 29px;
    background: var(--orange);
    color: var(--white);
    font-size: 17px;
    line-height: 29px;
    text-align: center;
  }
  .back-brand {
    position: absolute;
    left: 50%; top: 50%;
    width: 500px;
    transform: translate(-50%, -50%);
    color: var(--emboss);
    font-weight: 700;
    font-size: 40px;
    line-height: 46px;
    letter-spacing: 2px;
    text-transform: uppercase;
    text-align: center;
  }
</style>
</head>
<body>
  <section class="card card-front">
    <div class="brand-name">Coastline Premier Retreats</div>
    <div class="divider"></div>
    <div class="contact-block">
      <div class="person-name">DANIEL REYES</div>
      <div class="person-title">CEO/Founder</div>
      <div class="address">Po Box, 48 Harbor Lane<br>North America, AB 40210</div>
      <ul class="contact-list">
        <li><svg viewBox="0 0 12 12"><path d="M3 0h6a1 1 0 0 1 1 1v10a1 1 0 0 1-1 1H3a1 1 0 0 1-1-1V1a1 1 0 0 1 1-1zm0 1.5v7.5h6V1.5zM6 10a.6.6 0 1 0 0 1.2A.6.6 0 0 0 6 10z"/></svg>555.214.7300</li>
        <li><svg viewBox="0 0 12 12"><path d="M0 4c0-2 2.5-3 6-3s6 1 6 3v1H9V4H3v1H0zM2 6h8l1 5H1zm4 1.3a1.6 1.6 0 1 0 0 3.2 1.6 1.6 0 0 0 0-3.2z"/></svg>+34 600 000 412</li>
        <li><svg viewBox="0 0 12 12"><path d="M0 5l6-4 6 4v7H0zm1.2 1v5l3.5-2.5zm9.6 0L7.3 8.5 10.8 11zM6 8.3 2 11h8z"/></svg>info@coastlinepremierretreats.example</li>
        <li><svg viewBox="0 0 12 12"><path d="M6 0a6 6 0 1 1 0 12A6 6 0 0 1 6 0zM3 2.5 2 5l2 1 1 2.5 1.5-1L6 5 4.5 4zm5 .5L7 4.5l1.5 1.5L10 7.5l.5-2.5z"/></svg>www.coastlinepremierretreats.example</li>
      </ul>
    </div>
    <div class="tagline-band">Luxury Hotel &amp; Resort Email Marketing</div>
  </section>

  <section class="card card-back">
    <div class="back-brand">Coastline Premier Retreats</div>
  </section>
</body>
</html>
```